Business Card Design for Marketing Firm

Looking for business card design for higher end marketing firm. Clean but impressionable/trendy. We are a marketing firm that represents manufacturers in the foodservice equipment and supply industry. Our customers are end users such has hotels, restaurants, country clubs, convention centers and casinos as well as distributors of restaurants supplies and equipment, and manufacturers of foodservice equipment and supplies.
Target Market(s)
Hotels, Restaurants, Supply & Equipment Distributors, Foodservice Manufacturers
Industry/Entity Type
Foodservice/Hospitality
Contact Information for Business Card
Name, Title, Contact Number, Email, Website, Social Media, Address
Requirements
Must have
- Clean & Simple but Serious and Impressionable

```html
<!DOCTYPE html>
<html lang="en">
<head>
<meta charset="utf-8">
<title>Meridian Hospitality Reps — Business Card</title>
<link rel="stylesheet" href="https://fonts.googleapis.com/css2?family=Cinzel:wght@500;700&family=PT+Serif:wght@400;700&display=swap">
<style>
  :root {
    --navy: #2a2a78;
    --white: #ffffff;
    --silver: #bdbdc0;
    --backdrop-top: #e9e9e9;
    --backdrop-bottom: #bfbfbf;
  }
  html, body {
    margin: 0;
    width: 1200px;
    height: 856px;
    overflow: hidden;
  }
  body {
    background: linear-gradient(var(--backdrop-top), var(--backdrop-bottom));
    position: relative;
    font-family: "PT Serif", Georgia, serif;
  }
  .card {
    position: absolute;
    top: 279px;
    width: 520px;
    height: 297px;
    overflow: hidden;
    box-shadow: 0 10px 28px rgba(0, 0, 0, 0.35);
  }
  .card--front { left: 50px; background: var(--white); }
  .card--back  { left: 630px; background: var(--navy); }

  .card__wave { position: absolute; inset: 0; }

  .wordmark {
    position: absolute;
    font-family: "Cinzel", "Times New Roman", serif;
    font-weight: 500;
    letter-spacing: 0.04em;
    text-align: center;
    line-height: 1.15;
    margin: 0;
  }
  .wordmark--front {
    left: 20px;
    top: 128px;
    width: 230px;
    font-size: 19px;
    color: var(--navy);
  }
  .wordmark--back {
    left: 0;
    right: 0;
    top: 112px;
    font-size: 34px;
    color: var(--white);
  }
  .wordmark__sub { display: block; font-size: 0.7em; }

  .contact {
    position: absolute;
    right: 16px;
    top: 52px;
    color: var(--white);
    font-size: 10px;
    line-height: 1.5;
    text-align: right;
  }
  .contact__name {
    font-weight: 700;
    font-size: 13px;
    letter-spacing: 0.04em;
    margin: 0;
  }
  .contact__title { margin: 0 0 6px; }
  .contact__address { margin: 0 0 8px; }
  .contact__list { list-style: none; margin: 0; padding: 0; }
  .contact__item {
    display: flex;
    justify-content: flex-end;
    align-items: center;
    gap: 7px;
  }
  .contact__icon { width: 11px; height: 11px; flex: none; }
  .social-dot {
    width: 10px; height: 10px;
    margin: 0 0.5px;
    border-radius: 50%;
    background: var(--silver);
    flex: none;
  }
</style>
</head>
<body>

  <section class="card card--front" aria-label="Business card front">
    <svg class="card__wave" viewBox="0 0 520 297" width="520" height="297" aria-hidden="true">
      <path d="M352,0 C262,60 292,236 120,297" fill="none" stroke="var(--navy)" stroke-width="3"/>
      <path d="M366,0 C276,60 306,234 138,297 L520,297 L520,0 Z" fill="var(--silver)"/>
      <path d="M382,0 C292,60 322,232 160,297 L520,297 L520,0 Z" fill="var(--navy)"/>
    </svg>

    <p class="wordmark wordmark--front">Meridian Hospitality<span class="wordmark__sub">Reps</span></p>

    <div class="contact">
      <p class="contact__name">DANIEL WHITCOMBE</p>
      <p class="contact__title">Co-Founder</p>
      <p class="contact__address">P.O. BOX 44-12 EST-30<br>Harbor Ave 9, Lakeview</p>
      <ul class="contact__list">
        <li class="contact__item">555-301-2468
          <svg class="contact__icon" viewBox="0 0 12 12" aria-hidden="true"><path d="M3 1 L5 3.5 L4 5 Q5 7 7 8 L8.5 7 L11 9 L9.5 11 Q4 10.5 1 3 Z" fill="var(--white)"/></svg>
        </li>
        <li class="contact__item">info@meridianhospitality.com
          <svg class="contact__icon" viewBox="0 0 12 12" aria-hidden="true"><rect x="0.5" y="2.5" width="11" height="7" fill="var(--white)"/><path d="M0.5 2.5 L6 7 L11.5 2.5" fill="none" stroke="var(--navy)" stroke-width="1"/></svg>
        </li>
        <li class="contact__item">www.meridianhospitality.com
          <svg class="contact__icon" viewBox="0 0 12 12" aria-hidden="true"><circle cx="6" cy="6" r="5.2" fill="none" stroke="var(--white)" stroke-width="1.2"/><ellipse cx="6" cy="6" rx="2.2" ry="5.2" fill="none" stroke="var(--white)" stroke-width="1"/><path d="M0.8 6 H11.2" stroke="var(--white)" stroke-width="1"/></svg>
        </li>
        <li class="contact__item">@meridianhospitality
          <span class="social-dot" aria-hidden="true"></span>
        </li>
      </ul>
    </div>
  </section>

  <section class="card card--back" aria-label="Business card back">
    <p class="wordmark wordmark--back">Meridian Hospitality<span class="wordmark__sub">Reps</span></p>
  </section>

</body>
</html>
```